Accounting firm needing business card / letterhead designed
Marcus L. Trenholm, CPA
marcus@veltrowledger.com
www.veltrowledger.com
842 E Alder Ave Brenton, IN 43827
612-562-0974

```html
<!DOCTYPE html>
<html lang="en">
<head>
<meta charset="utf-8">
<title>Veltro Ledger — Business Card</title>
<link rel="stylesheet" href="https://fonts.googleapis.com/css2?family=Roboto:wght@400;700&family=Roboto+Condensed:wght@700&display=swap">
<style>
  :root {
    --backdrop: #e3e3e3;
    --paper: #f3f3f3;
    --navy: #24215a;
    --green: #87bd3b;
    --white: #ffffff;
  }
  html, body {
    margin: 0;
    padding: 0;
    width: 1200px;
    height: 960px;
    overflow: hidden;
    background: var(--backdrop);
  }
  .canvas {
    position: relative;
    width: 1200px;
    height: 960px;
    font-family: "Roboto", Arial, sans-serif;
  }
  .card {
    position: absolute;
    width: 600px;
    height: 343px;
    overflow: hidden;
    box-shadow: 0 2px 4px rgba(0,0,0,0.25);
  }
  .card-front { left: 314px; top: 113px; background: var(--paper); }
  .card-back  { left: 311px; top: 472px; background: var(--green); }

  .front-bands { position: absolute; inset: 0; }

  .wordmark {
    position: absolute;
    margin: 0;
    font-family: "Roboto", Arial, sans-serif;
    font-weight: 700;
    letter-spacing: 2px;
    white-space: nowrap;
  }
  .card-front .wordmark {
    left: 36px;
    top: 40px;
    font-size: 42px;
    color: var(--navy);
  }
  .card-back .wordmark {
    left: 0;
    right: 0;
    top: 122px;
    text-align: center;
    font-size: 56px;
    color: var(--white);
  }

  .holder-name {
    position: absolute;
    right: 33px;
    top: 228px;
    margin: 0;
    font-family: "Roboto Condensed", "Arial Narrow", sans-serif;
    font-weight: 700;
    font-size: 20px;
    color: var(--green);
    white-space: nowrap;
  }
  .contact-list {
    position: absolute;
    left: 35px;
    top: 258px;
    margin: 0;
    padding: 0;
    list-style: none;
    font-size: 14.5px;
    line-height: 19px;
    color: var(--white);
  }
  .contact-list li { display: flex; align-items: center; gap: 8px; white-space: nowrap; }
  .contact-list svg { width: 13px; height: 13px; fill: var(--green); flex: none; }

  .address {
    position: absolute;
    right: 33px;
    top: 277px;
    margin: 0;
    font-style: normal;
    font-size: 14.5px;
    line-height: 19px;
    text-align: right;
    color: var(--white);
    white-space: nowrap;
  }

  .back-url {
    position: absolute;
    left: 0;
    right: 0;
    top: 280px;
    margin: 0;
    text-align: center;
    font-size: 14px;
    letter-spacing: 6.5px;
    color: var(--white);
  }
</style>
</head>
<body>
<main class="canvas">

  <section class="card card-front" aria-label="Business card front">
    <svg class="front-bands" width="600" height="343" viewBox="0 0 600 343" aria-hidden="true">
      <polygon points="0,216 316,216 303,230 0,230" fill="var(--green)"/>
      <polygon points="0,232 301,232 336,197 600,197 600,343 0,343" fill="var(--navy)"/>
    </svg>

    <p class="wordmark">VELTRO LEDGER</p>

    <h1 class="holder-name">Marcus L. Trenholm, CPA</h1>

    <ul class="contact-list">
      <li>
        <svg viewBox="0 0 24 24" aria-hidden="true"><path d="M6.6 10.8a15.1 15.1 0 0 0 6.6 6.6l2.2-2.2c.3-.3.7-.4 1-.2 1.1.4 2.3.6 3.6.6.6 0 1 .4 1 1V20c0 .6-.4 1-1 1A17 17 0 0 1 3 4c0-.6.4-1 1-1h3.5c.6 0 1 .4 1 1 0 1.3.2 2.5.6 3.6.1.3 0 .7-.2 1z"/></svg>
        <span>612-562-0974</span>
      </li>
      <li>
        <svg viewBox="0 0 24 24" aria-hidden="true"><path d="M2 5h20v14H2z" /><path d="M2 5l10 8 10-8" fill="none" stroke="var(--navy)" stroke-width="2"/></svg>
        <span>marcus@veltrowledger.com</span>
      </li>
      <li>
        <svg viewBox="0 0 24 24" aria-hidden="true"><circle cx="12" cy="12" r="10"/><path d="M2 12h20M12 2c3 3 3 17 0 20M12 2c-3 3-3 17 0 20" fill="none" stroke="var(--navy)" stroke-width="1.6"/></svg>
        <span>www.veltrowledger.com</span>
      </li>
    </ul>

    <address class="address">842 E Alder Ave<br>Brenton, IN 43827</address>
  </section>

  <section class="card card-back" aria-label="Business card back">
    <p class="wordmark">VELTRO LEDGER</p>
    <p class="back-url">www.veltrowledger.com</p>
  </section>

</main>
</body>
</html>
```